Wordpress website design for children’s entertainment agency

What is the aim of the website?

The aim for the website is to attract potential bookers and to get them to respond to the Call to action: contact the entertainer - phone call/request a call back/completing a form.
All the information needs to be easy to access and navigate to, especially on mobile view.
The call to action needs to be clear and easy to navigate.

What I need:

Critical - This website needs to look good on all devices.
Easy navigation on a mobile device is essential so the elements need to be bold and easy to click on with a thumb (when in mobile view)

The ‘grid area’ needs to be graphics based with simple descriptions, i.e. ‘magic shows’, Circus Clowns, Face painting, Costume Characters, Party Host, Carnival Parties, Balloon Sculpting, DJ and MC, Princess Parties, Holiday Parties, Fun Add Ons and Contact.

See: http://www.jollymarvin.com/
and http://playtimebookingnest.com/

I would like to see a sample page layout as well to see how your design would be carried through the site layout in the inside pages.

Target Market(s)

The site visitors are mainly mums, aged between 25 - 41. Other visitors will included event organisers looking for entertainment services for baptism, communions and sweet 16’s

Industry/Entity Type

Entertainment Industry

Number of Pages Required

1 page

Font styles to use
Sans Serif

Colors
6c459b
fbed22
0493ce

Requirements
Must have
• Critical - This website needs to look good on all devices.
• Easy navigation on a mobile device is essential so the elements need to be bold and easy to click on with a thumb (when in mobile view)
• The ‘grid area’ needs to be graphics based with simple descriptions, i.e. ‘magic shows’, Circus Clowns, Face painting, Costume Characters, Party Host, Carnival Parties, Balloon Sculpting, DJ and MC, Princess Parties, Holiday Parties, Fun Add Ons and Contact.
• See: http://www.jollymarvin.com/
• and http://playtimebookingnest.com/
Nice to have
• clean looking and fun with an element of ‘Trobel’ and stars (this is the exciting site http://gordysjoyshack.com/index.html)

```html
<!DOCTYPE html>
<html lang="en">
<head>
<meta charset="utf-8">
<title>Pip's Party Patch – Children's Entertainment</title>
<link href="https://fonts.googleapis.com/css2?family=Fresca&family=Roboto:wght@400;500;700&family=Yanone+Kaffeesatz:wght@400;500&display=swap" rel="stylesheet">
<style>
:root{
  --sky-top:#7cc4ee;
  --sky-bottom:#e7f4fd;
  --violet:#5a4fd8;
  --star-a:#7c5ee8;
  --star-b:#4a7ff0;
  --yellow:#fbd021;
  --yellow-dark:#f3b300;
  --orange-line:#f29a13;
  --nav-text:#8a4a12;
  --green:#3cc41c;
  --green-dark:#2aa310;
  --red:#e2401f;
  --fb-blue:#3d5a9e;
  --footer-blue:#56c6e7;
  --footer-dark:#0d0d0d;
  --text:#7b7b7b;
  --field:#cdeef9;
  --submit:#0a86c6;
}
*{box-sizing:border-box;margin:0;padding:0}
html,body{width:958px;height:1200px;overflow:hidden}
body{position:relative;font-family:'Roboto',sans-serif;background:#fff}
.abs{position:absolute}

/* header */
.sky{left:0;top:0;width:958px;height:182px;background:linear-gradient(180deg,var(--sky-top),var(--sky-bottom) 70%,#f6fbff)}
.stars-bg{left:0;top:182px;width:958px;height:752px;background:radial-gradient(circle at 30% 40%,var(--star-a),transparent 60%),linear-gradient(135deg,var(--star-b),var(--star-a) 50%,var(--star-b))}
.brand{left:82px;top:50px;display:flex;align-items:center;gap:10px}
.brand-dot{width:30px;height:30px;border-radius:50%;background:var(--red)}
.brand-name{font-family:'Fresca',sans-serif;font-size:30px;color:var(--red);line-height:1;white-space:nowrap}
.call{right:121px;top:28px;text-align:right;font-family:'Yanone Kaffeesatz',sans-serif;white-space:nowrap}
.call small{display:block;font-size:14px;color:#222;line-height:1.1}
.call strong{display:block;font-size:21px;font-weight:400;color:#2a3fcf;line-height:1}
.call-icon{left:847px;top:30px;width:31px;height:31px;border-radius:50%;background:var(--violet);display:flex;align-items:center;justify-content:center}
.cta{left:748px;top:86px;width:130px;height:32px;background:linear-gradient(var(--green),var(--green-dark));border-radius:3px;color:#fff;font-family:'Yanone Kaffeesatz',sans-serif;font-size:20px;display:flex;align-items:center;justify-content:center;gap:6px;white-space:nowrap}

/* nav */
.nav-line{left:0;top:177px;width:958px;height:4px;background:var(--orange-line)}
.nav{left:78px;top:148px;width:800px;height:33px;display:flex;background:linear-gradient(var(--yellow),var(--yellow-dark))}
.nav a{font-family:'Yanone Kaffeesatz',sans-serif;font-size:13px;color:var(--nav-text);text-decoration:none;display:flex;align-items:center;justify-content:center;border-right:1px solid rgba(0,0,0,.08);white-space:nowrap}
.nav a.active{color:var(--red);background:rgba(255,255,255,.18)}

/* main */
.main{left:78px;top:181px;width:800px;height:753px;background:#fff}
.tile{width:123px}
.tile-img{width:123px;height:112px}
.tile-bar{height:4px}
.tile-label{font-family:'Fresca',sans-serif;font-size:15.5px;margin-top:8px;line-height:1;white-space:nowrap;letter-spacing:-.2px}

.qc-head{left:661px;top:200px;width:205px;height:40px;background:var(--red);color:#fff;font-family:'Fresca',sans-serif;font-size:20px;padding:8px 13px}
.qc-body{left:661px;top:240px;width:205px;height:268px;background:#e3e3e3}
.field{position:absolute;left:10px;width:185px;height:32px;background:#fff;font-size:8.5px;color:#999;padding:11px 10px}
.btn-submit{position:absolute;left:10px;top:219px;width:57px;height:26px;background:var(--green-dark);color:#fff;font-size:9.5px;font-weight:700;display:flex;align-items:center;justify-content:center}
.fb-head{left:661px;top:522px;width:205px;height:41px;background:var(--fb-blue);color:#fff;font-family:'Fresca',sans-serif;font-size:19px;padding:9px 13px;white-space:nowrap}
.fb-body{left:661px;top:563px;width:205px;height:116px;border:3px solid #e1e1e1;border-top:none;display:grid;grid-template-columns:repeat(4,1fr);padding:4px 6px;row-gap:2px}
.fan{display:flex;flex-direction:column;align-items:center;font-size:6px;color:#666}
.fan i{display:block;width:38px;height:38px;background:linear-gradient(#9aa3ad,#58606a);margin-bottom:3px}

.divider{left:78px;top:711px;width:800px;height:1px;background:#e2e2e2}
.about-title{left:92px;top:732px;font-family:'Fresca',sans-serif;font-size:27px;font-weight:400;color:var(--violet)}
.about-text{left:92px;top:773px;width:773px;font-size:8.6px;line-height:16.5px;color:var(--text)}
.about-text p{margin-bottom:9px}

/* footer */
.footer{left:0;top:934px;width:958px;height:203px;background:linear-gradient(180deg,var(--footer-blue),#7ad4ef)}
.f-title{position:absolute;z-index:2;font-weight:400;font-size:11px;color:#222;white-space:nowrap}
.map{left:79px;top:982px;width:165px;height:82px;background:linear-gradient(135deg,#eef0f2,#d9dde2)}
.info{left:260px;font-size:8.6px;color:#222;display:flex;gap:10px;line-height:13.5px;z-index:2}
.info svg{flex:none;margin-top:2px}
.vline{top:956px;width:1px;height:110px;background:rgba(255,255,255,.5)}
.ff{position:absolute;z-index:2;height:22px;background:var(--field);font-size:8.6px;color:#555;padding:6px 12px}
.ff-submit{background:var(--submit);color:#fff;text-align:center;padding:6px 0}
.links{font-size:8.6px;color:#222;line-height:18px;list-style:none;z-index:2;white-space:nowrap}
.links li::before{content:"• ";font-size:7px}
.bottom{left:0;top:1137px;width:958px;height:63px;background:var(--footer-dark)}
.copy{left:79px;top:1167px;font-size:9px;color:#ccc;white-space:nowrap}
.social{top:1163px;width:22px;height:22px;border-radius:50%}
</style>
</head>
<body>

<div class="abs sky" role="img" aria-label="Bright blue sky with soft white clouds"></div>
<div class="abs stars-bg" role="img" aria-label="Purple and blue background pattern of stars"></div>

<header>
  <div class="abs brand"><span class="brand-dot"></span><span class="brand-name">Pip's Party Patch</span></div>
  <div class="abs call"><small>Call us on</small><strong>718-555-0142</strong></div>
  <div class="abs call-icon">
    <svg width="14" height="14" viewBox="0 0 24 24" fill="#fff"><path d="M6.6 10.8a15.1 15.1 0 0 0 6.6 6.6l2.2-2.2a1 1 0 0 1 1-.25 11.4 11.4 0 0 0 3.6.6 1 1 0 0 1 1 1V20a1 1 0 0 1-1 1A17 17 0 0 1 3 4a1 1 0 0 1 1-1h3.5a1 1 0 0 1 1 1c0 1.25.2 2.45.6 3.6a1 1 0 0 1-.25 1z"/></svg>
  </div>
  <a class="abs cta">
    <svg width="16" height="12" viewBox="0 0 16 12" fill="none" stroke="#fff" stroke-width="1.5"><rect x="1" y="1" width="14" height="10" rx="1"/><path d="M1 1l7 6 7-6"/></svg>
    CONTACT US
  </a>
  <div class="abs nav-line"></div>
  <nav class="abs nav">
    <a class="active" style="width:96px">HOME</a>
    <a style="width:103px">ABOUT</a>
    <a style="width:139px">AREAS COVERED</a>
    <a style="width:108px">SEVICES</a>
    <a style="width:133px">TESTIMONIALS</a>
    <a style="width:110px">CONTACT</a>
    <a style="width:111px;border:none">FUN STUFF</a>
  </nav>
</header>

<main>
  <div class="abs main"></div>

  <div class="abs tile" style="left:92px;top:200px"><div class="tile-img" role="img" aria-label="Magician in a mask releasing a white dove" style="background:linear-gradient(135deg,#2b2b33,#5a3a6e)"></div><div class="tile-bar" style="background:#f0582a"></div><div class="tile-label" style="color:#e4502a">Magic Shows</div></div>
  <div class="abs tile" style="left:235px;top:200px"><div class="tile-img" role="img" aria-label="Circus clown in a striped costume" style="background:linear-gradient(135deg,#1a1a1a,#c8302a 60%,#f2b830)"></div><div class="tile-bar" style="background:#e8245a"></div><div class="tile-label" style="color:#e0245e">Circus Clowns</div></div>
  <div class="abs tile" style="left:378px;top:200px"><div class="tile-img" role="img" aria-label="Child with a painted superhero face" style="background:linear-gradient(135deg,#4a2b22,#a36650)"></div><div class="tile-bar" style="background:#a44b2a"></div><div class="tile-label" style="color:#9a4a2a">Face Painting</div></div>
  <div class="abs tile" style="left:521px;top:200px"><div class="tile-img" role="img" aria-label="Boy dressed as a pirate" style="background:linear-gradient(135deg,#6d665e,#c6453a 70%,#d9cfc2)"></div><div class="tile-bar" style="background:#f0b25a"></div><div class="tile-label" style="color:#f0a050">Costume Characters</div></div>

  <div class="abs tile" style="left:92px;top:371px"><div class="tile-img" role="img" aria-label="Party host with guests at an event" style="background:linear-gradient(135deg,#1a1c2e,#b23a3a 60%,#e1dcd2)"></div><div class="tile-bar" style="background:#5a4fd8"></div><div class="tile-label" style="color:#5a4fd8">Party Host</div></div>
  <div class="abs tile" style="left:235px;top:371px"><div class="tile-img" role="img" aria-label="Friends in carnival masks and hats" style="background:linear-gradient(135deg,#f2c640,#e83e7c 50%,#44b8e6)"></div><div class="tile-bar" style="background:#1e9ae0"></div><div class="tile-label" style="color:#1e8fd6">Carnival Parties</div></div>
  <div class="abs tile" style="left:378px;top:371px"><div class="tile-img" role="img" aria-label="Colourful balloon animals" style="background:linear-gradient(135deg,#e94b3c,#f2c53c 50%,#3e9ad8)"></div><div class="tile-bar" style="background:#2bb82a"></div><div class="tile-label" style="color:#2aa82a">Balloon Sculpting</div></div>
  <div class="abs tile" style="left:521px;top:371px"><div class="tile-img" role="img" aria-label="DJ at a mixing desk" style="background:linear-gradient(135deg,#8a8f96,#b12d8a 60%,#1c1c1c)"></div><div class="tile-bar" style="background:#c0242a"></div><div class="tile-label" style="color:#b82024">DJ and MC</div></div>

  <div class="abs tile" style="left:92px;top:542px"><div class="tile-img" role="img" aria-label="Little girl in a princess dress beside a pink cake" style="background:linear-gradient(135deg,#7a9a6a,#f2c6d6 60%,#e4e0ea)"></div><div class="tile-bar" style="background:#e8245a"></div><div class="tile-label" style="color:#e0245e">Princess Parties</div></div>
  <div class="abs tile" style="left:235px;top:542px"><div class="tile-img" role="img" aria-label="Two girls hugging at a birthday table" style="background:linear-gradient(135deg,#2a1c14,#d9a87a 55%,#e25a8a)"></div><div class="tile-bar" style="background:#5a4fd8"></div><div class="tile-label" style="color:#5a4fd8">Holiday Parties</div></div>
  <div class="abs tile" style="left:378px;top:542px"><div class="tile-img" role="img" aria-label="Child playing in a ball pit" style="background:linear-gradient(135deg,#2c6fd0,#e8403a 45%,#f2c83a 75%,#3aa84a)"></div><div class="tile-bar" style="background:#a44b2a"></div><div class="tile-label" style="color:#9a4a2a">Fun Add Ons</div></div>
  <div class="abs tile" style="left:521px;top:542px"><div class="tile-img" role="img" aria-label="Smiling woman on the phone" style="background:linear-gradient(135deg,#eef0f2,#b0c8d8 60%,#d8dde2)"></div><div class="tile-bar" style="background:#f0582a"></div><div class="tile-label" style="color:#e4502a">Contact</div></div>

  <aside>
    <div class="abs qc-head">Quick Contact</div>
    <form class="abs qc-body">
      <div class="field" style="top:12px">Name</div>
      <div class="field" style="top:53px">Email</div>
      <div class="field" style="top:94px">Phone</div>
      <div class="field" style="top:135px;height:72px">Message</div>
      <div class="btn-submit">SUBMIT</div>
    </form>
    <div class="abs fb-head">Find us on Friendbook</div>
    <div class="abs fb-body">
      <div class="fan"><i role="img" aria-label="Fan avatar"></i>Nina</div>
      <div class="fan"><i role="img" aria-label="Fan avatar"></i>Stevo</div>
      <div class="fan"><i role="img" aria-label="Fan avatar"></i>Sana</div>
      <div class="fan"><i role="img" aria-label="Fan avatar"></i>Milo</div>
      <div class="fan"><i role="img" aria-label="Fan avatar"></i>Karla</div>
      <div class="fan"><i role="img" aria-label="Fan avatar"></i>Kemal</div>
      <div class="fan"><i role="img" aria-label="Fan avatar"></i>Mara</div>
      <div class="fan"><i role="img" aria-label="Fan avatar"></i>Sami</div>
    </div>
  </aside>

  <div class="abs divider"></div>
  <h2 class="abs about-title">About Pip</h2>
  <div class="abs about-text">
    <p>Pellentesque a imperdiet dolor, et auctor est. Fusce sollicitudin lorem et luctus volutpat. Proin placerat dapibus gravida. In tristique tristique nulla eget hendrerit. Maecenas vel tortor accumsan quam varius imperdiet vel eget elit. Aenean facilisis tincidunt lectus, id dictum nisi luctus eget. Vivamus efficitur ex condimentum, malesuada eros eget, feugiat nibh. Sed tellus ex, imperdiet eget gravida sit amet, volutpat eget turpis. In nec ultricies est. Etiam mattis augue vehicula odio posuere, sit amet tempus lectus luctus. Nulla facilisi. Etiam vel massa elementum, bibendum tellus venenatis, feugiat massa. Curabitur venenatis lacinia ornare. Cras sollicitudin cursus dui eu placerat.</p>
    <p>Praesent elementum nulla sit amet justo pellentesque scelerisque. Nam et tortor in ante iaculis porttitor in luctus mi. Vivamus gravida sem a pretium euismod. Nam lobortis, purus et fringilla tempus, risus eros dignissim diam, eget finibus sem risus sit amet eros. Vestibulum facilisis dolor at purus tincidunt porta. Nam fringilla nulla vel nisl condimentum, dapibus condimentum enim porta. Phasellus blandit quam a ipsum gravida dapibus. Cras sed augue tortor. Suspendisse elit ligula, iaculis dignissim justo eu, vestibulum venenatis elit. Sed egestas, nisl id cursus ultricies, turpis orci rhoncus odio, id tristique odio ex in lacus. Nam suscipit sapien eget blandit sollicitudin.</p>
  </div>
</main>

<footer>
  <div class="abs footer" role="img" aria-label="Sky blue footer band with silhouettes of children playing"></div>
  <h4 class="f-title" style="left:79px;top:956px">Contact Details</h4>
  <div class="abs map" role="img" aria-label="Street map showing the office location"></div>
  <div class="abs info" style="top:982px">
    <svg width="8" height="10" viewBox="0 0 8 10"><path d="M4 0a3.5 3.5 0 0 0-3.5 3.5C.5 6 4 10 4 10s3.5-4 3.5-6.5A3.5 3.5 0 0 0 4 0zm0 5a1.4 1.4 0 1 1 0-2.8A1.4 1.4 0 0 1 4 5z" fill="#111"/></svg>
    <span>24 Building name, Street name<br>Harborview - Zipcode</span>
  </div>
  <div class="abs info" style="top:1020px">
    <svg width="9" height="9" viewBox="0 0 24 24" fill="#111"><path d="M6.6 10.8a15.1 15.1 0 0 0 6.6 6.6l2.2-2.2a1 1 0 0 1 1-.25 11.4 11.4 0 0 0 3.6.6 1 1 0 0 1 1 1V20a1 1 0 0 1-1 1A17 17 0 0 1 3 4a1 1 0 0 1 1-1h3.5a1 1 0 0 1 1 1c0 1.25.2 2.45.6 3.6a1 1 0 0 1-.25 1z"/></svg>
    <span>555 321 0485</span>
  </div>
  <div class="abs info" style="top:1047px">
    <svg width="10" height="8" viewBox="0 0 10 8"><rect width="10" height="8" fill="#111"/><path d="M0 0l5 4 5-4" stroke="#fff" fill="none"/></svg>
    <span>info@pipsparty.example</span>
  </div>

  <div class="abs vline" style="left:416px"></div>
  <h4 class="f-title" style="left:436px;top:956px">Contact us</h4>
  <div class="ff" style="left:436px;top:976px;width:112px">Name</div>
  <div class="ff" style="left:552px;top:976px;width:112px">Email</div>
  <div class="ff" style="left:436px;top:1009px;width:112px">Phone</div>
  <div class="ff" style="left:552px;top:1009px;width:112px">City</div>
  <div class="ff" style="left:436px;top:1042px;width:181px">Message</div>
  <div class="ff ff-submit" style="left:621px;top:1042px;width:43px">Submit</div>

  <div class="abs vline" style="left:684px"></div>
  <h4 class="f-title" style="left:700px;top:956px">Quick Links</h4>
  <ul class="abs links" style="left:700px;top:977px"><li>Home</li><li>About</li><li>Areas Covered</li><li>Sevices</li><li>Testimonials</li></ul>
  <ul class="abs links" style="left:783px;top:977px"><li>Contact</li><li>Fun stuff</li><li>Privacy Policy</li><li>Terms and Conditions</li><li>Sitemap</li></ul>

  <div class="abs bottom"></div>
  <p class="abs copy">Copyright © 2015 Pip. &nbsp; All rights reserved.</p>
  <span class="abs social" style="left:799px;background:#3d5a9e"></span>
  <span class="abs social" style="left:827px;background:#1e9ae0"></span>
  <span class="abs social" style="left:857px;background:#6bb84a"></span>
</footer>

</body>
</html>
```